Local Roofing/Construction company business needs new biz card design

We need a new business card design, current cards are from the start of this operation and generic at best. We are a local Construction Company (General Contractor) with a majority of our work originating from insurance claims-exterior finish work is the main focus (Roofs-Siding-Gutters etc). Heavily involved with homeowners and the low ball offers they receive from insurance company's after a insurable event takes place. I have attached some of our original logo file(s) below.

```html
<!DOCTYPE html>
<html lang="en">
<head>
<meta charset="utf-8">
<title>Stonefield Builders – Business Card</title>
<link rel="stylesheet" href="https://fonts.googleapis.com/css2?family=Open+Sans:wght@400;600;700;800&display=swap">
<style>
  :root {
    --bg: #222222;
    --ink-dark: #061c21;
    --ink-deep: #041619;
    --paper: #f1efec;
    --green: #4cb865;
    --text: #1d1d1d;
    --faint: #0c2a30;
  }
  * { box-sizing: border-box; margin: 0; padding: 0; }
  html, body { width: 1200px; height: 780px; overflow: hidden; }
  body {
    background: var(--bg);
    font-family: "Open Sans", Arial, sans-serif;
    display: flex;
    align-items: center;
    justify-content: center;
    gap: 40px;
  }
  .card {
    position: relative;
    width: 540px;
    height: 309px;
    border-radius: 3px;
    overflow: hidden;
    box-shadow: 0 18px 40px rgba(0,0,0,.45);
  }

  /* Front */
  .card-front { background: var(--paper); }
  .card-front .backdrop { position: absolute; inset: 0; width: 100%; height: 100%; }
  .brand-tag {
    position: absolute;
    top: 16px; left: 18px;
    background: var(--ink-dark);
    color: #fff;
    border-radius: 10px;
    padding: 9px 16px;
    display: flex; align-items: center; gap: 9px;
    font-weight: 800;
    font-size: 15px;
    letter-spacing: .06em;
    text-transform: uppercase;
  }
  .brand-square { width: 12px; height: 12px; background: var(--green); }
  .person {
    position: absolute;
    top: 76px; left: 0;
    padding-left: 24px;
    border-left: 8px solid var(--green);
  }
  .person-name { font-size: 22px; font-weight: 700; color: var(--ink-dark); line-height: 1.1; }
  .person-name .first { color: var(--green); }
  .person-role { font-size: 11px; color: var(--text); margin-top: 2px; }
  .address {
    position: absolute; top: 136px; left: 32px;
    font-size: 11px; line-height: 1.45; color: var(--text);
  }
  .contact-list {
    position: absolute; top: 176px; left: 20px;
    list-style: none;
    font-size: 11px; line-height: 1.5; color: var(--text);
  }
  .contact-list li { display: flex; align-items: center; gap: 6px; }
  .contact-list svg { width: 10px; height: 10px; flex: none; }
  .badge {
    position: absolute;
    right: 38px; top: 50%;
    transform: translateY(-50%);
    width: 150px;
    color: var(--paper);
    text-align: center;
    font-weight: 800;
    text-transform: uppercase;
    letter-spacing: .06em;
    font-size: 21px;
    line-height: 1.15;
  }
  .badge-square { width: 22px; height: 22px; background: var(--paper); margin: 0 auto 12px; }

  /* Back */
  .card-back { background: var(--ink-deep); display: flex; align-items: center; justify-content: center; }
  .back-name {
    color: var(--faint);
    font-weight: 800;
    font-size: 34px;
    letter-spacing: .08em;
    text-transform: uppercase;
    text-align: center;
    line-height: 1.1;
  }
</style>
</head>
<body>

  <section class="card card-front" aria-label="Business card front">
    <svg class="backdrop" viewBox="0 0 540 309" preserveAspectRatio="none" aria-hidden="true">
      <path d="M368 0 C 352 120, 300 170, 280 309 L 252 309 C 280 175, 340 120, 358 0 Z" fill="var(--green)"/>
      <path d="M372 0 C 356 124, 306 175, 286 309 L 540 309 L 540 0 Z" fill="var(--ink-dark)"/>
    </svg>

    <div class="brand-tag"><span class="brand-square"></span>Stonefield Builders</div>

    <div class="person">
      <p class="person-name"><span class="first">Dana</span> Whitlock</p>
      <p class="person-role">Co-Founder</p>
    </div>

    <p class="address">245 Oak Ridge Ln<br>Fairview, MO 63300</p>

    <ul class="contact-list">
      <li><svg viewBox="0 0 10 10"><path d="M2 1l2 2-1 1.2c.6 1.2 1.6 2.2 2.8 2.8L7 6l2 2-1.3 1.3C4.5 9 1 5.5.7 2.3z" fill="var(--green)"/></svg>555-201-4830</li>
      <li><svg viewBox="0 0 10 10"><path d="M2 1l2 2-1 1.2c.6 1.2 1.6 2.2 2.8 2.8L7 6l2 2-1.3 1.3C4.5 9 1 5.5.7 2.3z" fill="var(--green)"/></svg>555-201-7719 (Emergency)</li>
      <li><svg viewBox="0 0 10 10"><circle cx="5" cy="5" r="4.3" fill="none" stroke="var(--green)" stroke-width="1.2"/><path d="M.8 5h8.4M5 .8c-2 2.5-2 5.9 0 8.4M5 .8c2 2.5 2 5.9 0 8.4" fill="none" stroke="var(--green)" stroke-width=".9"/></svg>www.stonefieldbuilders.com</li>
      <li><svg viewBox="0 0 10 10"><rect x=".6" y="2" width="8.8" height="6.2" rx=".6" fill="var(--green)"/><path d="M1 2.5l4 3 4-3" fill="none" stroke="var(--paper)" stroke-width=".9"/></svg>hello@stonefieldbuilders.com</li>
    </ul>

    <div class="badge"><div class="badge-square"></div>Stonefield Builders</div>
  </section>

  <section class="card card-back" aria-label="Business card back">
    <p class="back-name">Stonefield<br>Builders</p>
  </section>

</body>
</html>
```